Letterhead for Conveyancing Company

Use existing logo to create a letterhead for a conveyancing company. Must be able to be used in Microsoft Word. Easy to read and professional.
Contact information to be at the bottom.
Bright Oak Conveyancing Pty Ltd
ACN 621 984 736PO Box 535 Campbelltown SA 5074
Mobile - 0461739286
Web address - www.brightoakconveyancing.com.au

Requirements
Must have
• Logo and contact details.
• Simple and professional.

```html
<!DOCTYPE html>
<html lang="en">
<head>
<meta charset="utf-8">
<title>Bright Oak Conveyancing — Letterhead</title>
<link href="https://fonts.googleapis.com/css2?family=Open+Sans:wght@400;600;700;800&display=swap" rel="stylesheet">
<style>
  :root {
    --backdrop: #d9dcdd;
    --paper: #ffffff;
    --magenta: #e0157f;
    --magenta-deep: #c8106f;
    --magenta-soft: #f6c6df;
    --charcoal: #6b6b6b;
    --text-grey: #5a5a5a;
    --watermark: #ececec;
    --rule: #d6d6d6;
  }
  * { margin: 0; padding: 0; box-sizing: border-box; }
  html, body {
    width: 1200px; height: 784px; overflow: hidden;
    background: var(--backdrop);
    font-family: "Open Sans", Arial, sans-serif;
  }
  .letterhead {
    position: absolute;
    left: 338px; top: 22px;
    width: 524px; height: 740px;
    background: var(--paper);
    box-shadow: 0 4px 14px rgba(0,0,0,0.12);
    overflow: hidden;
  }
  .header-band {
    position: absolute; left: 0; top: 0;
    width: 100%; height: 58px;
    background: linear-gradient(90deg, #fbe3ef 0%, var(--magenta-soft) 22%, #ec6fae 55%, var(--magenta) 78%, var(--magenta-deep) 100%);
  }
  .brand-tab {
    position: absolute; right: 0; top: 12px;
    width: 176px; height: 76px;
    background: var(--paper);
    border-top-left-radius: 8px;
    padding: 12px 16px 0 18px;
    text-align: right;
  }
  .brand-name {
    display: block;
    font-weight: 800;
    font-size: 25px;
    line-height: 1;
    letter-spacing: -0.5px;
    color: var(--magenta);
  }
  .brand-sub {
    display: block;
    margin-top: 6px;
    font-weight: 800;
    font-size: 11px;
    letter-spacing: 3.2px;
    color: var(--magenta);
  }
  .watermark {
    position: absolute; left: 40px; bottom: 70px;
    font-weight: 800;
    font-size: 48px;
    line-height: 0.95;
    letter-spacing: -1px;
    color: var(--watermark);
  }
  .contact-block {
    position: absolute; right: 26px; bottom: 34px;
    padding-left: 14px;
    border-left: 1px solid var(--rule);
    font-size: 8.5px;
    line-height: 1.75;
    color: var(--text-grey);
  }
  .contact-line { display: flex; align-items: center; gap: 5px; }
  .contact-line svg { width: 8px; height: 8px; flex: none; }
  .contact-line.address { color: var(--magenta); font-weight: 700; }
  .contact-sep { margin: 0 3px; }
</style>
</head>
<body>
  <main class="letterhead">
    <div class="header-band" role="img" aria-label="Pink faceted light-streak graphic band"></div>

    <div class="brand-tab">
      <span class="brand-name">Bright Oak</span>
      <span class="brand-sub">CONVEYANCING</span>
    </div>

    <div class="watermark" aria-hidden="true">Bright<br>Oak</div>

    <address class="contact-block">
      <div class="contact-line address">
        <svg viewBox="0 0 10 10"><circle cx="5" cy="5" r="5" fill="#e0157f"/><circle cx="5" cy="4.2" r="1.6" fill="#fff"/></svg>
        PO Box 871 Marlowdale SA 5096
      </div>
      <div class="contact-line">
        <svg viewBox="0 0 10 10"><circle cx="5" cy="5" r="5" fill="#e0157f"/><rect x="3" y="3" width="4" height="4" fill="#fff"/></svg>
        ACN 583 217 469
        <span class="contact-sep"></span>
        <svg viewBox="0 0 10 10"><circle cx="5" cy="5" r="5" fill="#e0157f"/><path d="M3.4 2.6 L4.6 3.8 L4 4.6 Q4.8 6 5.6 6.2 L6.4 5.6 L7.4 6.6 L6.6 7.6 Q3.2 7 2.6 3.4 Z" fill="#fff"/></svg>
        0461739286
      </div>
      <div class="contact-line">
        <svg viewBox="0 0 10 10"><circle cx="5" cy="5" r="5" fill="#e0157f"/><rect x="2.5" y="3.2" width="5" height="3.6" fill="#fff"/><path d="M2.5 3.2 L5 5.2 L7.5 3.2" stroke="#e0157f" stroke-width="0.6" fill="none"/></svg>
        contact@brightoakconveyancing.com.au
      </div>
      <div class="contact-line">
        <svg viewBox="0 0 10 10"><circle cx="5" cy="5" r="5" fill="#e0157f"/><circle cx="5" cy="5" r="2.4" fill="none" stroke="#fff" stroke-width="0.8"/></svg>
        www.brightoakconveyancing.com.au
      </div>
    </address>
  </main>
</body>
</html>
```